i need a business card for a plumbing company in california

we are a drain cleaning , maintenance plumbing company who is starting new marketing campaign for a tatrench-less pipe installation department .

Target Market(s)

the professional who appreciates time and quality workmanship.

Industry/Entity Type

Plumbing

Colors
0655a3
ec1f27

Requirements
Must have
• the second logo needs to be included
Nice to have
• a focus on the services offered
Should not have
• any underlined words on the brief

```html
<!DOCTYPE html>
<html lang="en">
<head>
<meta charset="utf-8">
<title>ClearFlow Plumbing – Business Card</title>
<link rel="stylesheet" href="https://fonts.googleapis.com/css2?family=Arimo:wght@400;700&family=Tinos&display=swap">
<style>
  :root {
    --blue: #0655a3;
    --navy: #0b3f86;
    --red: #ec1f27;
    --white: #ffffff;
    --ink-grey: #77766e;
    --stage: #2b2b2b;
  }
  * { box-sizing: border-box; margin: 0; padding: 0; }
  html, body { width: 1200px; height: 997px; overflow: hidden; }
  body {
    background: var(--stage);
    font-family: "Arimo", Arial, sans-serif;
    position: relative;
  }
  .card {
    position: absolute;
    width: 540px;
    height: 310px;
    border-radius: 18px;
    overflow: hidden;
    background: var(--white);
    top: 344px;
  }
  .card--back { left: 40px; }
  .card--front { left: 620px; }
  .card svg.card__art { position: absolute; inset: 0; }
  .logo {
    position: absolute;
    display: flex;
    align-items: center;
    gap: 8px;
    color: var(--ink-grey);
    font-weight: 700;
    font-size: 30px;
    line-height: 1;
    letter-spacing: -0.5px;
  }
  .logo__mark { width: 22px; height: 22px; background: var(--red); flex: none; }
  .card--back .logo { top: 34px; right: 34px; }
  .card--front .logo { top: 40px; right: 36px; }

  /* back side steps */
  .step {
    position: absolute;
    font-size: 11px;
    font-weight: 700;
    letter-spacing: 0.5px;
    text-transform: uppercase;
  }
  .step--red { color: var(--red); }
  .step--blue { color: var(--blue); }
  .step__num {
    position: absolute;
    width: 40px; height: 40px;
    border-radius: 50%;
    background: var(--navy);
    border: 3px solid var(--white);
    box-shadow: 0 0 0 2px var(--navy);
    color: var(--white);
    font-family: "Tinos", serif;
    font-size: 28px;
    display: flex; align-items: center; justify-content: center;
  }
  .motto {
    position: absolute;
    left: -14px; top: 262px;
    width: 210px; height: 30px;
    background: var(--blue);
    border-radius: 15px;
    color: var(--white);
    font-size: 12px; font-weight: 700;
    display: flex; align-items: center; justify-content: center; gap: 5px;
  }
  .motto__accent { background: var(--white); color: var(--red); padding: 1px 4px; border-radius: 2px; }

  /* front side contact */
  .person { position: absolute; left: 24px; top: 170px; }
  .person__name { color: var(--red); font-weight: 700; font-size: 14px; letter-spacing: 0.5px; }
  .person__role { color: var(--white); font-size: 13px; margin-top: 4px; }
  .contact {
    position: absolute; left: 24px; top: 218px;
    list-style: none;
    font-family: "Tinos", serif;
    color: var(--white);
    font-size: 14px;
  }
  .contact li { display: flex; align-items: center; gap: 8px; height: 18px; }
  .contact svg { width: 10px; height: 10px; flex: none; }
  .social {
    position: absolute; right: 26px; top: 140px;
    list-style: none;
    font-family: "Tinos", serif;
    color: var(--white);
    font-size: 13px;
    text-align: right;
  }
  .social li { display: flex; justify-content: flex-end; align-items: center; gap: 6px; height: 19px; }
  .social__dot { width: 9px; height: 9px; border-radius: 50%; background: var(--white); flex: none; }
  .social__badge { width: 26px; height: 14px; background: var(--white); opacity: 0.9; }
  .services {
    position: absolute; left: 0; right: 0; bottom: 8px;
    text-align: center;
    color: var(--white);
    font-weight: 700;
    font-size: 13px;
    letter-spacing: 0.3px;
  }
</style>
</head>
<body>

<section class="card card--back" aria-label="Card back">
  <svg class="card__art" viewBox="0 0 540 310" aria-hidden="true">
    <path d="M-10 250 C 90 215 150 150 270 140 S 440 90 550 40" fill="none" stroke="#ec1f27" stroke-width="12"/>
    <path d="M-10 264 C 90 229 150 164 270 154 S 440 104 550 54" fill="none" stroke="#0655a3" stroke-width="10"/>
  </svg>
  <div class="logo"><span class="logo__mark"></span>ClearFlow Plumbing</div>

  <div class="step__num" style="left:76px;top:176px">1</div>
  <div class="step step--red" style="left:86px;top:228px">Contact us.</div>
  <div class="step__num" style="left:250px;top:128px">2</div>
  <div class="step step--blue" style="left:262px;top:180px">Buy online</div>
  <div class="step__num" style="left:425px;top:82px">3</div>
  <div class="step step--red" style="left:418px;top:134px">Social media us</div>

  <div class="motto">LEAD BY <span class="motto__accent">EXAMPLE</span></div>
</section>

<section class="card card--front" aria-label="Card front">
  <svg class="card__art" viewBox="0 0 540 310" aria-hidden="true">
    <path d="M0 150 C 120 105 210 100 300 118 S 470 140 540 88 L540 310 L0 310 Z" fill="#ec1f27"/>
    <path d="M0 166 C 120 121 210 116 300 134 S 470 156 540 104 L540 278 L0 278 Z" fill="#0b3f86"/>
  </svg>
  <div class="logo"><span class="logo__mark"></span>ClearFlow Plumbing</div>

  <div class="person">
    <p class="person__name">MARCO REYES</p>
    <p class="person__role">Owner</p>
  </div>

  <ul class="contact">
    <li><svg viewBox="0 0 10 10"><rect x="2" y="0.5" width="6" height="9" rx="1" fill="none" stroke="#fff"/></svg>209 555-0148</li>
    <li><svg viewBox="0 0 10 10"><rect x="0.5" y="2" width="9" height="6" fill="#fff"/></svg>info@clearflowplumbing.com</li>
    <li><svg viewBox="0 0 10 10"><path d="M1 9 L9 1" stroke="#fff" stroke-width="2"/></svg>www.clearflowplumbing.com</li>
  </ul>

  <ul class="social">
    <li><span class="social__dot"></span>/ClearFlowPlumb</li>
    <li><span class="social__dot"></span>@ClearFlowPlumb</li>
    <li><span class="social__dot"></span><span class="social__dot"></span><span class="social__dot"></span><span class="social__badge"></span></li>
  </ul>

  <p class="services">Sewer Drain Cleaning — Maintenance — Trenchless Re-Pipes</p>
</section>

</body>
</html>
```